Lanternfield Drinks business cards

We need a business card design for our new logo. The company is modern, progressive, professional, yet approachable. The key products are ready to drink bottles and cans of coffee based beverages.
These cards will be a critical part of the first impression made by our sales organization, business development team, and all external facing personnel.
Card can be a vertical or horizontal orientation.

Target Market(s)

Customers, suppliers, business partners

Industry/Entity Type

Business

Contact Information for Business Card

Business cards should feature Company Name and Logo.

Font styles to use
Serif

Colors

Designer to choose colors to be used in the design.

Requirements
Must have
• Strong readability of Name, phone #, mobile number and email address.
• Job title, website url, Street Address, and other details can be secondary level readability.
Nice to have
• High impact, simplistic quality design.
• Ok to utilize the 'H in the box' separate from the company name

```html
<!DOCTYPE html>
<html lang="en">
<head>
<meta charset="utf-8">
<title>Lanternfield Drinks — Business Cards</title>
<link href="https://fonts.googleapis.com/css2?family=Cinzel:wght@700&family=PT+Sans:wght@400;700&display=swap" rel="stylesheet">
<style>
  :root {
    --stage: #e4e2df;
    --paper: #fbfbfa;
    --orange: #ef5a24;
    --orange-light: #f7961e;
    --gold: #f2a33a;
    --ink: #4a4a4a;
    --white: #ffffff;
  }
  * { box-sizing: border-box; margin: 0; padding: 0; }
  html, body { width: 1200px; height: 844px; overflow: hidden; }
  body {
    background: var(--stage);
    font-family: "PT Sans", sans-serif;
    position: relative;
  }
  .card {
    position: absolute;
    top: 267px;
    width: 540px;
    height: 309px;
    box-shadow: 0 6px 18px rgba(0,0,0,0.18);
  }
  .card-front { left: 40px; background: var(--paper); }
  .card-back {
    left: 620px;
    background: linear-gradient(200deg, var(--orange-light) 0%, var(--orange) 75%);
    display: flex;
    flex-direction: column;
    align-items: center;
    justify-content: center;
  }

  /* front */
  .brand {
    position: absolute;
    top: 48px;
    left: 0;
    right: 0;
    display: flex;
    align-items: center;
    justify-content: center;
    gap: 12px;
  }
  .brand-square {
    width: 40px;
    height: 40px;
    background: var(--orange);
  }
  .brand-name {
    font-family: "Cinzel", serif;
    font-weight: 700;
    font-size: 26px;
    letter-spacing: 0.5px;
    color: var(--orange);
  }
  .divider {
    position: absolute;
    left: 34px;
    right: 34px;
    top: 128px;
    height: 1px;
    background: var(--gold);
  }
  .person {
    position: absolute;
    left: 34px;
    top: 150px;
  }
  .person-name {
    font-family: "Cinzel", serif;
    font-weight: 700;
    font-size: 20px;
    color: var(--orange);
    letter-spacing: 0.3px;
  }
  .person-title {
    font-size: 14px;
    color: var(--ink);
    margin-top: 1px;
  }
  .address {
    position: absolute;
    left: 34px;
    top: 206px;
    font-size: 14px;
    color: var(--ink);
  }
  .divider-short {
    position: absolute;
    left: 34px;
    top: 234px;
    width: 220px;
    height: 1px;
    background: var(--gold);
  }
  .contacts {
    position: absolute;
    left: 34px;
    top: 244px;
    font-size: 14px;
    color: var(--ink);
    line-height: 1.45;
  }
  .contacts .label { color: var(--orange); }
  .contacts .row span + span { margin-left: 8px; }
  .contacts .web { color: var(--orange); }

  /* back */
  .back-square {
    width: 110px;
    height: 110px;
    border: 6px solid var(--white);
  }
  .back-name {
    font-family: "Cinzel", serif;
    font-weight: 700;
    font-size: 18px;
    color: var(--white);
    letter-spacing: 1px;
    margin-top: 16px;
  }
  .back-url {
    font-family: "Cinzel", serif;
    font-weight: 700;
    font-size: 13px;
    letter-spacing: 1.5px;
    color: var(--white);
    margin-top: 16px;
  }
</style>
</head>
<body>
  <section class="card card-front">
    <div class="brand">
      <div class="brand-square"></div>
      <div class="brand-name">Lanternfield Drinks</div>
    </div>
    <div class="divider"></div>
    <div class="person">
      <div class="person-name">DANIEL HARTLEY</div>
      <div class="person-title">Managing Director</div>
    </div>
    <div class="address">12345, Address Goes Here Country Name, 123456.</div>
    <div class="divider-short"></div>
    <div class="contacts">
      <div class="row">
        <span><span class="label">T:</span>(044) 123 456 789</span>
        <span><span class="label">F:</span>(044) 123456789</span>
        <span><span class="label">M:</span>(044)123456789</span>
      </div>
      <div class="row">
        <span><span class="label">E:</span>info@youremail.com</span>
        <span class="web">www.yourweb.com</span>
      </div>
    </div>
  </section>

  <section class="card card-back">
    <div class="back-square"></div>
    <div class="back-name">Lanternfield Drinks</div>
    <div class="back-url">WWW.WEBNAME.COM</div>
  </section>
</body>
</html>
```